Veldmark Supplies Business Card

Professional business card that stand out to our potential customers. Front and back with clean modern design

Industry/Entity Type

Oil and gas

Contact Information for Business Card

Name, address, website , office phone and cell number

Requirements
Must have
• Editable files for each employee

```html
<!DOCTYPE html>
<html lang="en">
<head>
<meta charset="utf-8">
<title>Veldmark Supplies Business Card</title>
<link rel="stylesheet" href="https://fonts.googleapis.com/css2?family=Arimo:wght@400;700&display=swap">
<style>
  :root {
    --stage: #3d3d3d;
    --card-light: #ffffff;
    --card-dark: #2f2f2f;
    --brand-red: #ff0000;
    --brand-cyan: #06aed5;
    --ink: #3a3a3a;
  }
  * { margin: 0; padding: 0; box-sizing: border-box; }
  html, body {
    width: 1200px; height: 803px; overflow: hidden;
    background: var(--stage);
    font-family: "Arimo", Arial, sans-serif;
  }
  .stage { position: relative; width: 1200px; height: 803px; }
  .card {
    position: absolute; top: 253px;
    width: 520px; height: 297px;
    border-radius: 18px;
    box-shadow: 0 18px 40px rgba(0,0,0,.45);
    overflow: hidden;
  }
  .card--front { left: 50px; background: var(--card-light); border-bottom: 4px solid var(--brand-cyan); }
  .card--back { left: 630px; background: var(--card-dark); border-bottom: 3px solid var(--brand-cyan); }

  .wordmark {
    display: flex; align-items: center; gap: 8px;
    font-weight: 700; text-transform: uppercase;
    color: var(--brand-red); letter-spacing: .04em;
  }
  .wordmark__square { background: var(--brand-red); display: block; }

  .card--front .wordmark { position: absolute; left: 36px; top: 40px; font-size: 17px; }
  .card--front .wordmark__square { width: 14px; height: 14px; }
  .brand-square {
    position: absolute; right: 52px; top: 56px;
    width: 150px; height: 150px;
    border: 10px solid var(--brand-red);
  }

  .person { position: absolute; left: 36px; top: 92px; }
  .person__name { font-weight: 700; font-size: 22px; color: var(--brand-red); }
  .person__role { font-size: 12px; color: var(--brand-cyan); margin-top: 2px; }

  .address { position: absolute; left: 36px; top: 150px; font-size: 12px; color: var(--ink); line-height: 1.4; }
  .contacts { position: absolute; left: 36px; top: 194px; list-style: none; font-size: 12px; color: var(--ink); }
  .contacts li { display: flex; align-items: center; gap: 8px; line-height: 1.45; }
  .contacts svg { width: 11px; height: 11px; flex: none; }

  .card--back .wordmark {
    position: absolute; left: 50%; top: 50%;
    transform: translate(-50%, -50%);
    font-size: 24px; gap: 12px;
  }
  .card--back .wordmark__square { width: 20px; height: 20px; }
</style>
</head>
<body>
<main class="stage">
  <section class="card card--front" aria-label="Business card front">
    <div class="wordmark"><span class="wordmark__square"></span>Veldmark Supplies</div>
    <div class="brand-square" aria-hidden="true"></div>
    <div class="person">
      <p class="person__name">Daniel Reyes</p>
      <p class="person__role">President</p>
    </div>
    <p class="address">4120 Harlow Street<br>Midland, Texas 79701</p>
    <ul class="contacts">
      <li><svg viewBox="0 0 12 12"><path d="M3 1l2 2-1 1.5c.8 1.6 1.9 2.7 3.5 3.5L9 7l2 2-1.5 2C5 10.5 1.5 7 1 2.5z" fill="#ff0000"/></svg>555-210-4836</li>
      <li><svg viewBox="0 0 12 12"><rect x="3" y="1" width="6" height="10" rx="1" fill="none" stroke="#ff0000" stroke-width="1.4"/></svg>555-210-7719</li>
      <li><svg viewBox="0 0 12 12"><rect x="1" y="2.5" width="10" height="7" fill="#ff0000"/><path d="M1 2.5l5 4 5-4" fill="none" stroke="#fff" stroke-width="1"/></svg>info@veldmarksupplies.com</li>
      <li><svg viewBox="0 0 12 12"><circle cx="6" cy="6" r="5" fill="none" stroke="#ff0000" stroke-width="1.4"/><path d="M1 6h10M6 1c-2.5 3-2.5 7 0 10M6 1c2.5 3 2.5 7 0 10" fill="none" stroke="#ff0000" stroke-width="1"/></svg>www.veldmarksupplies.com</li>
    </ul>
  </section>

  <section class="card card--back" aria-label="Business card back">
    <div class="wordmark"><span class="wordmark__square"></span>Veldmark Supplies</div>
  </section>
</main>
</body>
</html>
```